Give Gold Kite an Online Presence!

Gold Kite Property Maintenance is an Australian Owned property maintenance company who needs a stand out online presence.

GK maintains many buildings and sites and wants to appeal to a corporate professional market with their brand new website. GK is essentially a handyman service offering all maintenance services to home owners, office managers, real estate agents and strata managers.

The Website:
We need a corporate website that appeals to our broader customer base (property owners, property managers, office managers) the copy is being written by a professional so use filler text for now.

Things that we want:
Home page that sets us apart and appeals to the corporate and residential market. The home page needs to not focus on either the residential or commercial market. The home page should focus on our logo and branding. We have a logo already and it is attached to the brief, please use it and try to consider the colour pallette that goes with it. Whilst we want the site to appear strong and manly it is important to remember that 95% of our customers are female so we need the site to be appealing to women. Women need to believe that we are strong, dependable and trustworthy.
We'd like a quote page and potentially also the ability to get a quote from the home page (please don't put it in if it ruins the overall feel of the home page)
An "about us" page
A contact us page
A blog that's built in (we don't want to link to an external blog)
(overall we'd expect to have 6 or 7 pages total)

The site will also need coding - we expect this to be done in a separate project but need you to consider a few things about the coding side of things.

It needs to be iPhone and iPad compatible.

We'd like you to suggest the best CMS that you would use or if you would suggest not using a CMS please let us know with your submissions.

Target Market(s)

Property owners, office managers and property managers who need maintenance on buildings (So all of them)

Industry/Entity Type

Property Maintenance

Requirements
Must have
• Our Logo
Home page
About Us
Residential
Commercial
Real Estate/Strata
Contact Us/Quote
Blog
Nice to have
• Quote form included in home page
Movement on the home page at least
Should not have
• other logos, too much colour
NO FLASH

```html
<!DOCTYPE html>
<html lang="en">
<head>
<meta charset="utf-8">
<title>Gold Kite Property Maintenance</title>
<link rel="stylesheet" href="https://fonts.googleapis.com/css2?family=PT+Sans+Narrow:wght@400;700&family=PT+Sans:wght@400;700&display=swap">
<style>
:root{
  --orange:#f7921e;
  --dark:#2b2b2b;
  --text:#3a3a3a;
  --grey:#dcdcdc;
  --grey-dark:#bdbdbd;
  --line:#cfcfcf;
  --white:#ffffff;
}
*{box-sizing:border-box;margin:0;padding:0}
html,body{width:1200px;height:1163px;overflow:hidden;background:var(--white)}
body{position:relative;font-family:"PT Sans",sans-serif;color:var(--text)}
.abs{position:absolute}
.top-rule{left:0;top:0;width:1200px;height:3px;background:var(--dark)}
.bottom-rule{left:0;top:1160px;width:1200px;height:3px;background:var(--dark)}

.brand{left:160px;top:22px;display:flex;align-items:center;gap:8px;font-family:"PT Sans Narrow",sans-serif;font-weight:700;font-size:24px;color:var(--dark)}
.brand-mark{width:22px;height:22px;background:var(--orange)}

.phone-tab{left:870px;top:3px;width:171px;height:30px;background:var(--dark);clip-path:polygon(0 0,100% 0,100% 100%,30px 100%);display:flex;align-items:center;justify-content:flex-end;gap:10px;padding-right:14px;color:var(--white);font-family:"PT Sans Narrow",sans-serif;font-size:19px}

.main-nav{right:159px;top:60px;display:flex;font-family:"PT Sans Narrow",sans-serif;font-size:18px}
.main-nav a{color:var(--dark);text-decoration:none;padding:0 8px;border-left:1px solid var(--line);line-height:22px}
.main-nav a:first-child{border-left:none}
.main-nav a:last-child{padding-right:0}
.main-nav a.active{color:var(--orange)}

.slider{left:157px;top:98px;width:885px;height:320px;background:var(--grey);padding:7px 8px 10px 9px}
.slide{position:relative;width:100%;height:100%;background:var(--white);overflow:hidden}
.slide-photo{position:absolute;right:0;top:0;width:560px;height:100%;background:linear-gradient(90deg,#ffffff 0%,#f1ece8 30%,#e9e2dc 60%,#f4efe9 100%)}
.slide-title{position:absolute;left:43px;top:72px;font-family:"PT Sans Narrow",sans-serif;font-size:33px;line-height:38px;color:var(--orange);font-weight:400}
.pager{position:absolute;left:3px;top:272px;display:flex;background:var(--grey);height:29px;padding:0 4px}
.pager span{width:36px;display:flex;align-items:center;justify-content:center;font-family:"PT Sans Narrow",sans-serif;font-size:14px;color:var(--dark);border-left:1px solid #b9b9b9;margin:3px 0}
.pager span:first-child{border-left:none;background:var(--orange);color:var(--dark);margin:0;width:24px}

.card{top:440px;width:285px;height:158px;background:var(--grey);padding:7px}
.card-photo{width:100%;height:143px}
.card-res{left:157px}
.card-res .card-photo{background:linear-gradient(180deg,#8fc0ea 0%,#b8d6ee 35%,#a45a3e 55%,#7e4a36 80%,#4b8a3a 100%)}
.card-com{left:456px}
.card-com .card-photo{background:linear-gradient(135deg,#cfe6f7 0%,#6fb0dd 45%,#2f7db4 75%,#1b4f78 100%)}
.card-link{top:609px;width:282px;height:30px;border-bottom:1px solid var(--line);display:flex;align-items:center;gap:10px;padding-left:7px;font-family:"PT Sans Narrow",sans-serif;font-size:18px;color:var(--orange)}

.blog-box{left:757px;top:440px;width:285px;height:158px;background:var(--orange);padding:12px 14px;color:var(--white);font-size:11.5px;line-height:15px}
.blog-box h3{font-family:"PT Sans Narrow",sans-serif;font-weight:700;font-size:19px;margin-bottom:8px;color:var(--white)}
.blog-box p{margin-bottom:9px}
.blog-box p.excerpt{color:var(--dark)}
.blog-nav{left:762px;top:638px;width:282px;border-top:1px solid var(--line)}
.blog-arrows{left:993px;top:608px;display:flex;gap:6px}
.round-btn{width:22px;height:22px;border-radius:50%;background:#d5d5d5;display:flex;align-items:center;justify-content:center}

.section-title{top:670px;font-family:"PT Sans Narrow",sans-serif;font-weight:700;font-size:19px;color:var(--orange)}
.panel{top:705px;height:170px;border:1px solid var(--line);border-bottom:6px solid var(--grey-dark);padding:12px 14px;font-size:12px;line-height:18.5px}
.services{left:157px;width:587px}
.services p{text-align:justify;margin-bottom:13px}
.testimonial{left:764px;width:280px;padding:16px 22px 12px 40px}
.testimonial p{text-align:justify;font-size:12px;line-height:18.5px}
.quote-mark{font-family:"PT Sans Narrow",sans-serif;font-weight:700;color:var(--orange);font-size:40px;line-height:1}

.divider-title{left:157px;width:888px;display:flex;align-items:center;gap:10px;font-family:"PT Sans Narrow",sans-serif;font-size:18px;color:var(--orange)}
.divider-title::before,.divider-title::after{content:"";height:1px;background:var(--line);flex:1}

.form-label{font-size:12px;color:var(--text)}
.field{border:1px solid var(--line);background:var(--white)}
.submit{left:939px;top:983px;width:79px;height:31px;background:var(--orange);color:var(--white);font-size:14px;display:flex;align-items:center;justify-content:center;clip-path:polygon(7px 0,100% 0,100% 100%,7px 100%,7px 62%,0 50%,7px 38%)}

.footer-links{left:157px;top:1124px;font-size:10px;color:var(--text)}
.footer-links a{color:var(--text);text-decoration:none}
.footer-links span{margin:0 5px}
.copyright{right:156px;top:1124px;font-size:10px}
</style>
</head>
<body>
<div class="abs top-rule"></div>

<div class="abs brand"><span class="brand-mark"></span>Gold Kite</div>

<div class="abs phone-tab">
  <svg width="16" height="18" viewBox="0 0 16 18" aria-hidden="true"><path d="M4 1 L7 5 L5 7 C6 10 8 12 10 13 L12 11 L15 14 L12 17 C6 16 1 10 1 4 Z" fill="#ffffff"/></svg>
  415.XXX.XXXX
</div>

<nav class="abs main-nav">
  <a class="active" href="#">Home</a>
  <a href="#">About Us</a>
  <a href="#">Residential</a>
  <a href="#">Commercial</a>
  <a href="#">Real Estate/Strata</a>
  <a href="#">Contact Us/Quote</a>
  <a href="#">Blog</a>
</nav>

<section class="abs slider">
  <div class="slide">
    <div class="slide-photo" role="img" aria-label="Woman holding a small model house"></div>
    <h1 class="slide-title">Commercial and Residential<br>Property Maintenance</h1>
    <div class="pager"><span>1</span><span>2</span><span>3</span><span>4</span></div>
  </div>
</section>

<div class="abs card card-res"><div class="card-photo" role="img" aria-label="Brick family home with garage"></div></div>
<div class="abs card card-com"><div class="card-photo" role="img" aria-label="Glass office tower against blue sky"></div></div>

<div class="abs card-link" style="left:157px">
  <svg width="8" height="12" viewBox="0 0 8 12" aria-hidden="true"><path d="M1 1 L6 6 L1 11" stroke="#2b2b2b" stroke-width="2.2" fill="none"/></svg>
  Residential Property
</div>
<div class="abs card-link" style="left:456px">
  <svg width="8" height="12" viewBox="0 0 8 12" aria-hidden="true"><path d="M1 1 L6 6 L1 11" stroke="#2b2b2b" stroke-width="2.2" fill="none"/></svg>
  Commercial Property
</div>

<aside class="abs blog-box">
  <h3>LATEST BLOG ENTRIES</h3>
  <p>05/10/2012 - Harnessing technology to streamline operations in a property maintenance businessa</p>
  <p class="excerpt">How Ridgeline harness new technology and use an integrated, system-driven approach to job management</p>
</aside>
<div class="abs blog-nav"></div>
<div class="abs blog-arrows">
  <span class="round-btn"><svg width="8" height="11" viewBox="0 0 8 11" aria-hidden="true"><path d="M6 1 L2 5.5 L6 10" stroke="#2b2b2b" stroke-width="2.2" fill="none"/></svg></span>
  <span class="round-btn"><svg width="8" height="11" viewBox="0 0 8 11" aria-hidden="true"><path d="M2 1 L6 5.5 L2 10" stroke="#2b2b2b" stroke-width="2.2" fill="none"/></svg></span>
</div>

<h2 class="abs section-title" style="left:157px">Property Maintenance &amp; Facilities Management Services</h2>
<h2 class="abs section-title" style="left:764px">What Our Customers Are Saying</h2>

<div class="abs panel services">
  <p>Your property matters to us, which is why at Ridgeline we go the extra mile to offer you premium-quality building maintenance services. Our skilled workforce of reliable professionals is on hand around the clock for all your property maintenance needs. We use only the most highly skilled tradesmen, from decorators and gas engineers to electricians and plumbers.</p>
  <p>Gold Kite always employs the most appropriate professional tradesmen for the job, regardless of its size or nature. Our customer-focused technicians, engineers and handymen are all dedicated to their trade. Their professional work ethics go a long way to dispel common criticisms of the building industry.</p>
</div>

<div class="abs panel testimonial">
  <span class="abs quote-mark" style="left:17px;top:12px">“</span>
  <p>Our properties had been neglected by the previous owners and we needed an immediate impact from a seasoned provider. We saved almost $250,000.00 the first year with Harwood Property Maintenance. <span class="quote-mark" style="font-size:34px;vertical-align:-14px">”</span></p>
</div>

<div class="abs divider-title" style="top:904px">Quick Contact</div>

<label class="abs form-label" style="left:186px;top:958px">Name</label>
<div class="abs field" style="left:270px;top:954px;width:266px;height:24px"></div>
<label class="abs form-label" style="left:186px;top:995px">E mail id</label>
<div class="abs field" style="left:270px;top:992px;width:266px;height:24px"></div>
<label class="abs form-label" style="left:186px;top:1029px">Phone</label>
<div class="abs field" style="left:270px;top:1029px;width:266px;height:24px"></div>
<label class="abs form-label" style="left:580px;top:958px">Message</label>
<div class="abs field" style="left:634px;top:954px;width:251px;height:101px"></div>
<div class="abs submit">Submit</div>

<div class="abs divider-title" style="top:1084px">Links</div>

<div class="abs footer-links">
  <a href="#">Home</a><span>|</span><a href="#">About Us</a><span>|</span><a href="#">Residential</a><span>|</span><a href="#">Commercial</a><span>|</span><a href="#">Real Estate/Strata</a><span>|</span><a href="#">Contact Us/Quote</a><span>|</span><a href="#">Blog</a>
</div>
<div class="abs copyright">Copyrights @ 2012 All Rights Reserved</div>

<div class="abs bottom-rule"></div>
</body>
</html>
```